Brightway Carpet and Tile cleaning Business card Design

I need a design that has the same feel as my van.
i would also like a prominent "Review us on facebook" somewhere, but not that it makes it look silly.
I would like the card to have a little bit of grey or black in the design as well.

It will need contact details
phone: 0455 817264
email: rkbrightwayclean@mailbox-example.com
website: www.brightwaycarpetandtilecleaning-example.com.au
facebook: /brightwaycarpetandtilecleaning

Industry/Entity Type

Business

Contact Information for Business Card

Phone number 0455817264
Email rkbrightwayclean@mailbox-example.com
Website www.brightwaycarpetandtilecleaning-example.com.au
Facebook/brightwaycarpetandtilecleaning

Colors
000000

Requirements
Must have
• Same feel as my van
• I want the card to stand out from the crowd
Nice to have
• Maybe include a tiny bit of a third colour? Grey's,blacks, orange?

```html
<!DOCTYPE html>
<html lang="en">
<head>
<meta charset="utf-8">
<title>Brightway Clean – Business Card</title>
<link href="https://fonts.googleapis.com/css2?family=Exo+2:wght@700;800&family=Open+Sans:wght@400;600&display=swap" rel="stylesheet">
<style>
  :root {
    --stage: #3b3b3b;
    --paper: #ffffff;
    --brand-green: #8cc63f;
    --brand-green-deep: #7ab530;
    --brand-green-light: #a6d465;
    --brand-blue: #16b1e0;
    --brand-blue-deep: #0ea2d3;
    --brand-grey: #6d6e71;
    --ink-light: #ffffff;
  }
  * { margin: 0; padding: 0; box-sizing: border-box; }
  html, body {
    width: 1105px; height: 1200px; overflow: hidden;
    background: var(--stage);
  }
  .sheet { position: relative; width: 1105px; height: 1200px; }
  .card {
    position: absolute; left: 192px; width: 720px; height: 412px;
    overflow: hidden; box-shadow: 0 6px 14px rgba(0,0,0,.45);
  }
  .card--front { top: 146px; background: var(--paper); }
  .card--back { top: 602px; }

  .front-waves { position: absolute; inset: 0; }

  .brand-mark {
    position: absolute; left: 330px; top: 62px; width: 360px;
    text-align: right;
    font-family: "Exo 2", sans-serif;
  }
  .brand-mark__name {
    display: flex; align-items: center; justify-content: flex-end; gap: 10px;
    font-weight: 800; font-size: 44px; line-height: 1; color: var(--brand-grey);
  }
  .brand-mark__dot {
    width: 18px; height: 18px; border-radius: 50%; background: var(--brand-blue);
    flex: none;
  }
  .brand-mark__tagline {
    margin-top: 6px; font-weight: 700; font-size: 17px; letter-spacing: 2px;
    color: var(--brand-grey);
  }

  .contact-list {
    position: absolute; left: 30px; top: 276px; list-style: none;
    font-family: "Open Sans", sans-serif; font-size: 16.5px; color: var(--ink-light);
  }
  .contact-list__item {
    display: flex; align-items: center; gap: 11px; height: 27px;
  }
  .contact-list__icon { width: 18px; height: 18px; flex: none; }

  .card-holder {
    position: absolute; right: 34px; top: 327px; text-align: right;
    font-family: "Exo 2", sans-serif; color: var(--ink-light); line-height: 1.2;
  }
  .card-holder__name { font-weight: 800; font-size: 25px; letter-spacing: .5px; }
  .card-holder__role { font-weight: 700; font-size: 19px; }

  .back-fill {
    position: absolute; inset: 0;
    background:
      linear-gradient(115deg, transparent 52%, rgba(255,255,255,.14) 56%, rgba(255,255,255,.08) 70%, transparent 74%),
      radial-gradient(circle at 30% 40%, var(--brand-green-light), var(--brand-green) 55%, var(--brand-green-deep));
  }
  .brand-mark--reversed {
    left: 0; right: 0; top: 168px; width: auto; text-align: center; color: var(--ink-light);
  }
  .brand-mark--reversed .brand-mark__name { justify-content: center; color: var(--ink-light); font-size: 52px; }
  .brand-mark--reversed .brand-mark__dot { background: var(--ink-light); }
  .brand-mark--reversed .brand-mark__tagline { color: var(--ink-light); font-size: 19px; }

  .review-callout {
    position: absolute; left: 0; right: 0; top: 346px;
    display: flex; justify-content: center; align-items: center; gap: 8px;
    font-family: "Exo 2", sans-serif; font-weight: 800; font-size: 18px;
    color: var(--ink-light); letter-spacing: .5px;
  }
  .review-callout__square { width: 15px; height: 15px; background: var(--ink-light); }
</style>
</head>
<body>
<main class="sheet">

  <section class="card card--front" aria-label="Business card front">
    <svg class="front-waves" viewBox="0 0 720 412" width="720" height="412" aria-hidden="true">
      <path d="M0 228 C110 175 220 168 340 225 S575 320 720 228 L720 412 L0 412 Z" fill="var(--brand-green)"/>
      <path d="M0 262 C110 212 220 205 340 262 S575 345 720 262 L720 412 L0 412 Z" fill="var(--brand-blue)"/>
    </svg>

    <div class="brand-mark">
      <div class="brand-mark__name"><span class="brand-mark__dot"></span>Brightway Clean</div>
      <div class="brand-mark__tagline">CARPET &amp; TILE CLEANING</div>
    </div>

    <ul class="contact-list">
      <li class="contact-list__item">
        <svg class="contact-list__icon" viewBox="0 0 24 24" aria-hidden="true"><path fill="#fff" d="M6.6 10.8a15 15 0 0 0 6.6 6.6l2.2-2.2c.3-.3.7-.4 1-.2 1.1.4 2.3.6 3.6.6.6 0 1 .4 1 1V20c0 .6-.4 1-1 1A17 17 0 0 1 3 4c0-.6.4-1 1-1h3.5c.6 0 1 .4 1 1 0 1.3.2 2.5.6 3.6.1.3 0 .7-.2 1z"/></svg>
        <span>0455817264</span>
      </li>
      <li class="contact-list__item">
        <svg class="contact-list__icon" viewBox="0 0 24 24" aria-hidden="true"><rect x="2" y="5" width="20" height="14" rx="1.5" fill="#fff"/><path d="M3 6.5l9 6.5 9-6.5" fill="none" stroke="var(--brand-blue)" stroke-width="1.8"/></svg>
        <span>rkbrightwayclean@mailbox-example.com</span>
      </li>
      <li class="contact-list__item">
        <svg class="contact-list__icon" viewBox="0 0 24 24" aria-hidden="true"><circle cx="12" cy="12" r="9.5" fill="none" stroke="#fff" stroke-width="2"/><ellipse cx="12" cy="12" rx="4" ry="9.5" fill="none" stroke="#fff" stroke-width="1.6"/><path d="M2.5 12h19" stroke="#fff" stroke-width="1.6"/></svg>
        <span>www.brightwaycarpetandtilecleaning-example.com.au</span>
      </li>
      <li class="contact-list__item">
        <svg class="contact-list__icon" viewBox="0 0 24 24" aria-hidden="true"><rect x="3" y="3" width="18" height="18" fill="#fff"/></svg>
        <span>brightwaycarpetandtilecleaning</span>
      </li>
    </ul>

    <div class="card-holder">
      <div class="card-holder__name">DANIEL REEVE</div>
      <div class="card-holder__role">CEO/FOUNDER</div>
    </div>
  </section>

  <section class="card card--back" aria-label="Business card back">
    <div class="back-fill" role="img" aria-label="Green background with soft soap bubble texture"></div>
    <div class="brand-mark brand-mark--reversed">
      <div class="brand-mark__name"><span class="brand-mark__dot"></span>Brightway Clean</div>
      <div class="brand-mark__tagline">CARPET &amp; TILE CLEANING</div>
    </div>
    <div class="review-callout">REVIEW US ON <span class="review-callout__square"></span></div>
  </section>

</main>
</body>
</html>
```